Business Card Design with existing logo

BrightWren provides inspirational leadership training and coaching for corporate executives. We focus on being challenging, humorous and compassionate, providing the right mix of support and push for individuals and teams to improve their knowledge and performance. The colour purple is essential to the design. We already have a logo we are very happy with - we are curious to see what can be done to come across in a professional, high standard way that sets us apart. Ideally the design should include the photo of Liesel-Joy
Target Market(s)
HR/ Senior Management 500 - 1500 employees
Industry/Entity Type
Leadership
Contact Information for Business Card
BrightWren Coaching Ltd
Inspirational leadership
Liesel-Joy Korhonen Bramwick
Leadership coach and trainer
Telephone: +44 1632 960 418
Mobile: +44 7700 900 562
e-mail: lieseljoy@brightwrencoaching.example
www.brightwrencoaching.example
Requirements
Must have
- The existing logo
Picture of Liesel-Joy

```html
<!DOCTYPE html>
<html lang="en">
<head>
<meta charset="utf-8">
<title>BrightWren Coaching – Business Cards</title>
<link href="https://fonts.googleapis.com/css2?family=Open+Sans:wght@400;600&display=swap" rel="stylesheet">
<style>
  :root {
    --purple: #6a3d9a;
    --ink: #1d1d1f;
    --grey: #5a5a5e;
    --paper: #ffffff;
    --backdrop: #d9d9db;
    --stripe: #111111;
  }
  * { margin: 0; padding: 0; box-sizing: border-box; }
  html, body { width: 1200px; height: 985px; overflow: hidden; }
  body {
    background: var(--backdrop);
    font-family: "Open Sans", Arial, sans-serif;
    color: var(--ink);
    position: relative;
  }
  .card {
    position: absolute;
    left: 300px;
    width: 600px;
    height: 340px;
    background: var(--paper);
    border-radius: 22px;
    overflow: hidden;
    box-shadow: 0 10px 24px rgba(0,0,0,0.18);
  }
  .card--back { top: 110px; }
  .card--front { top: 520px; }

  /* back side */
  .brand-disc {
    position: absolute;
    left: 55px; top: -10px;
    width: 270px; height: 270px;
    border-radius: 50%;
    background: var(--purple);
  }
  .back-brand {
    position: absolute;
    left: 272px; top: 236px;
  }
  .brand-name {
    font-weight: 600;
    text-transform: uppercase;
    color: var(--purple);
    letter-spacing: 0.04em;
    white-space: nowrap;
  }
  .back-brand .brand-name { font-size: 22px; line-height: 28px; }
  .brand-tagline {
    font-size: 9px;
    letter-spacing: 0.42em;
    text-transform: uppercase;
    color: var(--grey);
    white-space: nowrap;
  }
  .back-brand .brand-tagline { margin-top: 2px; padding-left: 40px; }

  /* front side */
  .side-band { position: absolute; left: 0; top: 0; }
  .front-brand {
    position: absolute;
    left: 170px; top: 28px;
    display: flex; align-items: center; gap: 10px;
  }
  .brand-dot {
    width: 44px; height: 44px; border-radius: 50%;
    background: var(--purple); flex: none;
  }
  .front-brand .brand-name { font-size: 22px; }
  .front-brand .brand-tagline { font-size: 7.5px; margin-top: 1px; }
  .contact {
    position: absolute;
    left: 175px; top: 98px;
    right: 40px;
    font-size: 14px;
    line-height: 17px;
  }
  .contact__name { font-size: 21px; line-height: 26px; }
  .contact__role {
    color: var(--purple);
    display: flex; align-items: flex-end; gap: 2px;
  }
  .contact__role::after {
    content: ""; flex: 1; height: 1px; background: var(--purple); margin-bottom: 3px;
  }
  .contact__block { margin-top: 12px; }
  .accent { color: var(--purple); }
</style>
</head>
<body>

<section class="card card--back" aria-label="Business card back">
  <div class="brand-disc"></div>
  <div class="back-brand">
    <div class="brand-name">BrightWren Coaching</div>
    <div class="brand-tagline">Inspirational leadership</div>
  </div>
</section>

<section class="card card--front" aria-label="Business card front">
  <svg class="side-band" width="600" height="340" viewBox="0 0 600 340">
    <polygon points="0,0 150,0 40,340 0,340" fill="var(--purple)"/>
    <line x1="162" y1="0" x2="52" y2="340" stroke="var(--stripe)" stroke-width="5"/>
    <g fill="none" stroke="#fff" stroke-width="1.6">
      <path d="M22 222 q0 10 10 10 l2-3 -3-3 -2 1 q-3-1 -4-4 l1-2 -3-3z" fill="#fff" stroke="none"/>
      <rect x="23" y="240" width="8" height="13" rx="1.5"/>
      <rect x="21" y="262" width="13" height="9" rx="1"/>
      <path d="M21 262 l6.5 5 6.5-5"/>
      <circle cx="27.5" cy="286" r="6"/>
      <path d="M21.5 286 h12 M27.5 280 q-4 6 0 12 q4-6 0-12"/>
    </g>
  </svg>

  <div class="front-brand">
    <div class="brand-dot"></div>
    <div>
      <div class="brand-name">BrightWren Coaching</div>
      <div class="brand-tagline">Inspirational leadership</div>
    </div>
  </div>

  <div class="contact">
    <div class="contact__name">Liesel-Joy Korhonen Bramwick</div>
    <div class="contact__role">Leadership coach and trainer</div>
    <div>BrightWren Coaching Ltd</div>
    <div>Inspirational leadership</div>
    <div class="contact__block">
      <div>+44 1632 960 418</div>
      <div>+44 7700 900 562 (Mobile)</div>
      <div>lieseljoy@brightwrencoaching.example</div>
      <div>www.<span class="accent">brightwrencoaching</span>.example</div>
    </div>
  </div>
</section>

</body>
</html>
```